Lumavento business card

We need a modern business card - With our 4 colors - See web: www.lumavento.dk

I have attached logo and som old business Cards we have - Lets Make the new ones shine...:-) -

Industry/Entity Type

Business

Requirements
Must have
• the logo with lumavento only,

```html
<!DOCTYPE html>
<html lang="da">
<head>
<meta charset="utf-8">
<title>Lumavento – visitkort</title>
<link href="https://fonts.googleapis.com/css2?family=Open+Sans:wght@400;600;700&display=swap" rel="stylesheet">
<style>
  :root {
    --plum: #7a1676;
    --plum-dark: #6a1167;
    --lime: #95c11f;
    --ink: #1c1c1c;
    --paper: #ffffff;
    --backdrop: #e9e9ec;
  }
  * { box-sizing: border-box; margin: 0; padding: 0; }
  html, body { width: 1200px; height: 864px; overflow: hidden; }
  body {
    background: var(--backdrop);
    font-family: "Open Sans", Arial, sans-serif;
    position: relative;
  }
  .card {
    position: absolute;
    left: 340px;
    width: 520px;
    height: 300px;
    border-radius: 3px;
    box-shadow: 0 6px 18px rgba(0,0,0,.15);
  }
  /* Front side */
  .card-front {
    top: 92px;
    background: var(--plum);
    color: var(--paper);
    text-align: center;
  }
  .front-wordmark {
    position: absolute;
    top: 92px; left: 0; right: 0;
    font-size: 38px;
    font-weight: 600;
    letter-spacing: 3px;
  }
  .front-rule {
    position: absolute;
    top: 176px; left: 120px;
    width: 280px; height: 3px;
    background: var(--paper);
  }
  .front-name {
    position: absolute;
    top: 150px; left: 0; right: 0;
    font-size: 16px;
    letter-spacing: 1.5px;
  }
  .front-title {
    position: absolute;
    top: 182px; left: 0; right: 0;
    font-size: 15px;
    letter-spacing: 1.5px;
  }
  .front-rule-bottom {
    position: absolute;
    top: 208px; left: 120px;
    width: 280px; height: 3px;
    background: var(--paper);
  }
  /* Back side */
  .card-back {
    top: 474px;
    background: var(--paper);
    color: var(--ink);
  }
  .holder {
    position: absolute;
    left: 34px; top: 112px;
  }
  .holder-name {
    color: var(--plum);
    font-weight: 700;
    font-size: 20px;
    line-height: 1.1;
  }
  .holder-title { font-size: 13px; }
  .brand {
    position: absolute;
    left: 300px; top: 56px;
    width: 196px;
    text-align: center;
  }
  .brand-name {
    color: var(--lime);
    font-weight: 600;
    font-size: 24px;
    letter-spacing: 3px;
  }
  .brand-rule {
    height: 3px;
    background: var(--lime);
    margin: 8px 0 6px;
  }
  .brand-tagline { font-size: 13px; }
  .contacts {
    position: absolute;
    right: 24px; top: 176px;
    list-style: none;
    text-align: right;
    font-size: 14px;
    line-height: 22px;
  }
  .contacts li { display: flex; justify-content: flex-end; align-items: center; gap: 8px; }
  .contacts svg { width: 12px; height: 12px; fill: var(--plum); }
  .address {
    position: absolute;
    left: 0; right: 24px; bottom: 18px;
    text-align: right;
    font-size: 14px;
  }
</style>
</head>
<body>

<section class="card card-front" aria-label="Visitkort forside">
  <div class="front-wordmark">lumavento</div>
  <div class="front-name" style="top:150px">Maren Holtved</div>
  <div class="front-rule"></div>
  <div class="front-title">Salgsdirektør</div>
  <div class="front-rule-bottom"></div>
</section>

<section class="card card-back" aria-label="Visitkort bagside">
  <div class="holder">
    <div class="holder-name">Maren Holtved</div>
    <div class="holder-title">Salgsdirektor</div>
  </div>

  <div class="brand">
    <div class="brand-name">lumavento</div>
    <div class="brand-rule"></div>
    <div class="brand-tagline">Medier til unge</div>
  </div>

  <ul class="contacts">
    <li>+45 40 12 34 56
      <svg viewBox="0 0 24 24" aria-hidden="true"><path d="M6.6 10.8a15.1 15.1 0 0 0 6.6 6.6l2.2-2.2a1 1 0 0 1 1-.25 11.4 11.4 0 0 0 3.6.57 1 1 0 0 1 1 1V20a1 1 0 0 1-1 1A17 17 0 0 1 3 4a1 1 0 0 1 1-1h3.5a1 1 0 0 1 1 1c0 1.25.2 2.45.57 3.6a1 1 0 0 1-.25 1z"/></svg>
    </li>
    <li>mh@lumavento.dk
      <svg viewBox="0 0 24 24" aria-hidden="true"><path d="M2 5h20v14H2z M2 5l10 8 10-8" fill="var(--plum)" stroke="#fff" stroke-width="1.5"/></svg>
    </li>
    <li>www.lumavento.dk
      <svg viewBox="0 0 24 24" aria-hidden="true"><circle cx="12" cy="12" r="11"/><path d="M1 12h22M12 1c4 4 4 18 0 22M12 1c-4 4-4 18 0 22" stroke="#fff" stroke-width="1.5" fill="none"/></svg>
    </li>
  </ul>

  <div class="address">Lærkevej 18 - 4000 Roskilde - Tlf. 36 21 47 80</div>
</section>

</body>
</html>
```